High-end construction company needs a business card design

We need a modern looking business card that draws people in, is memorable and looks so good people will want to sick it on their fridges.
On the first side what is needed are:
Logo
My name - Tomasz Brelwik
Title - Managing Director
Website - www.varkelt.co.uk
Email - tomasz@varkelt.co.uk
Telephone - 020 5194 6281
Mobile - 07845139072
On the back side was is needed is a list of all the services we provide:
-Kitchen Renovations
-Bathroom Renovations
-House Renovations
-Garage Conversions
-Extensions
-Loft Conversions
-Conservatories
-Carpentry
-Tiling
-Electrical
-Plumbing & Heating
-Bricklaying
-Landscaping
-Decorating
-Plastering
We would like the colours to be the same shades as on the logo with grey or black for the words.
Target Market(s)
Anyone who needs building work done
Contact Information for Business Card
This business card is for a construction company which strives to deliver excellent service and quality.
The look and feel of the card should represent this.
Requirements
Must have
- On the first side what is needed are:
Logo
My name - Tomasz Brelwik
Title - Managing Director
Website - www.varkelt.co.uk
Email - tomasz@varkelt.co.uk
Telephone - 020 5194 6281
Mobile - 07845139072
Nice to have
- Cool looking features

```html
<!DOCTYPE html>
<html lang="en">
<head>
<meta charset="utf-8">
<title>Varkelt Construction Ltd – Business Card</title>
<link href="https://fonts.googleapis.com/css2?family=Montserrat:wght@300;400;600;800&display=swap" rel="stylesheet">
<style>
  :root{
    --green:#5cb83c;
    --green-deep:#3f9a2c;
    --green-dark:#2f7d22;
    --ink:#4a4a4a;
    --ink-soft:#6a6a6a;
    --paper:#ffffff;
    --ground:#e9ebe9;
  }
  *{margin:0;padding:0;box-sizing:border-box}
  html,body{width:1200px;height:965px;overflow:hidden;background:var(--ground);font-family:"Montserrat",sans-serif}
  .card{position:absolute;width:640px;height:414px;overflow:hidden;box-shadow:0 10px 30px rgba(0,0,0,.18)}

  /* back side */
  .card--back{left:60px;top:56px;background:radial-gradient(ellipse at 55% 25%,#6cc24a 0%,var(--green) 40%,var(--green-deep) 100%)}
  .back-brand{position:absolute;left:0;right:0;top:40px;text-align:center;color:var(--paper)}
  .back-brand .brand-name{font-weight:800;font-size:54px;letter-spacing:3px;line-height:1}
  .back-brand .brand-sub{font-weight:800;font-size:15px;letter-spacing:4px;margin-top:8px}
  .services{position:absolute;left:40px;right:0;bottom:28px;height:210px;background:var(--paper);border-radius:0 40px 0 40px;
    display:flex;flex-direction:column;justify-content:center;align-items:center;gap:14px;padding:0 24px}
  .services p{font-size:12.5px;font-weight:400;color:var(--ink);letter-spacing:0;text-transform:uppercase;white-space:nowrap;line-height:1.2}
  .services .dot{display:inline-block;width:8px;height:8px;border-radius:50%;background:var(--green);margin:0 5px;vertical-align:1px}

  /* front side */
  .card--front{left:500px;top:490px;background:var(--paper)}
  .front-brand{position:absolute;left:42px;top:210px;display:flex;align-items:center;gap:12px}
  .front-brand .mark{width:34px;height:34px;background:var(--green)}
  .front-brand .brand-name{font-weight:800;font-size:48px;letter-spacing:2px;color:var(--green);line-height:1}
  .front-brand .brand-sub{font-weight:800;font-size:14px;letter-spacing:4px;color:var(--green);margin-top:6px}
  .person{position:absolute;left:390px;top:46px}
  .person .name{font-weight:800;font-size:22px;color:var(--green);text-transform:uppercase;letter-spacing:.5px}
  .person .title{font-weight:400;font-size:15px;color:var(--ink-soft);margin-top:2px}
  .contacts{position:absolute;left:420px;top:150px;list-style:none}
  .contacts li{display:flex;align-items:center;gap:10px;font-size:15px;font-weight:300;color:var(--ink);margin-bottom:6px}
  .contacts svg{width:15px;height:15px;flex:none}
  .website{position:absolute;left:420px;top:290px;font-size:17px;font-weight:300;color:var(--ink)}
  .website b{color:var(--green);font-weight:800}
  .dash{position:absolute;left:505px;top:352px;width:18px;height:2px;background:var(--green)}
</style>
</head>
<body>

<section class="card card--back" aria-label="Back of card: services">
  <div class="back-brand">
    <div class="brand-name">VARKELT</div>
    <div class="brand-sub">CONSTRUCTION LTD</div>
  </div>
  <div class="services">
    <p>Kitchen Renovations<span class="dot"></span>Bathroom Renovations<span class="dot"></span>House Renovations</p>
    <p>Garage Conversions<span class="dot"></span>Extensions<span class="dot"></span>Loft Conversions<span class="dot"></span>Conservatories</p>
    <p>Carpentry<span class="dot"></span>Tiling<span class="dot"></span>Electrical<span class="dot"></span>Plumbing &amp; Heating</p>
    <p>Bricklaying<span class="dot"></span>Landscaping<span class="dot"></span>Decorating<span class="dot"></span>Plastering</p>
  </div>
</section>

<section class="card card--front" aria-label="Front of card: contact">
  <div class="front-brand">
    <div class="mark"></div>
    <div>
      <div class="brand-name">VARKELT</div>
      <div class="brand-sub">CONSTRUCTION LTD</div>
    </div>
  </div>

  <div class="person">
    <div class="name">Tomasz Brelwik</div>
    <div class="title">Managing Director</div>
  </div>

  <ul class="contacts">
    <li>
      <svg viewBox="0 0 16 16" fill="none" stroke="#5cb83c" stroke-width="1.4"><rect x="4" y="1" width="8" height="14" rx="1.5"/><line x1="7" y1="12.5" x2="9" y2="12.5"/></svg>
      07845139072
    </li>
    <li>
      <svg viewBox="0 0 16 16" fill="none" stroke="#5cb83c" stroke-width="1.4"><path d="M3 2l3 0 1 3-2 1.5a8 8 0 0 0 4.5 4.5L11 9l3 1v3a1 1 0 0 1-1 1A11 11 0 0 1 2 3a1 1 0 0 1 1-1z"/></svg>
      020 5194 6281
    </li>
    <li>
      <svg viewBox="0 0 16 16" fill="none" stroke="#5cb83c" stroke-width="1.4"><rect x="1.5" y="3.5" width="13" height="9"/><path d="M1.5 3.5L8 9l6.5-5.5"/></svg>
      tomasz@varkelt.co.uk
    </li>
  </ul>

  <div class="website">www.<b>varkelt.co</b>.uk</div>
  <div class="dash"></div>
</section>

</body>
</html>
```